Verodex business card

Business card for sustainable investment company called "Verodex". Verodex is an exchange platform selling carbon credits between buyers and sellers. Carbon Credits are an environmental commodity for reducing global carbon emissions.

the card should obviously have our logo and the theme should be sustainability/environment mixed with a trading platform.

Contact Information for Business Card

Logo, Name, Title, Phone, Email

Colors
0054AA
0677BA
7BADD7
CADEEF
E8F1F8
0094D4
00A9DD
6FCCEA
C7EBF8
E9F6FB
00AB8E
00BBA5
67D7C9
C6EFE9
E9F9F6
59FF00
82FF00
B8FF75
E3FFCB
F4FFEA

```html
<!DOCTYPE html>
<html lang="en">
<head>
<meta charset="utf-8">
<title>Verodex Business Card</title>
<link href="https://fonts.googleapis.com/css2?family=Montserrat:wght@400;500;600;700&display=swap" rel="stylesheet">
<style>
  :root {
    --page: #ecedef;
    --paper: #ffffff;
    --ink: #16233f;
    --band-start: #35b7ea;
    --band-end: #4a7fcf;
    --back-start: #4a72cc;
    --back-end: #5cc4e6;
    --white: #ffffff;
    --rule: rgba(255,255,255,0.6);
  }
  * { box-sizing: border-box; margin: 0; padding: 0; }
  html, body { width: 1200px; height: 786px; overflow: hidden; }
  body {
    background: var(--page);
    font-family: "Montserrat", sans-serif;
    position: relative;
  }
  .card {
    position: absolute;
    top: 243px;
    width: 520px;
    height: 300px;
    overflow: hidden;
    box-shadow: 0 10px 28px rgba(0,0,0,0.18);
  }
  .card-front { left: 50px; background: var(--paper); }
  .card-back {
    left: 630px;
    background: linear-gradient(135deg, var(--back-start), var(--back-end));
  }

  /* front */
  .brand-front {
    position: absolute;
    left: 70px;
    top: 44px;
    display: flex;
    align-items: center;
    gap: 16px;
  }
  .brand-mark {
    width: 46px; height: 46px;
    border-radius: 50%;
    background: var(--band-start);
  }
  .brand-name {
    font-weight: 700;
    font-size: 42px;
    letter-spacing: 1px;
    color: var(--ink);
  }
  .band {
    position: absolute;
    left: 0; right: 0;
    top: 128px;
    height: 104px;
    background: linear-gradient(90deg, var(--band-start), var(--band-end));
    display: flex;
    align-items: center;
    padding-left: 70px;
  }
  .person { text-align: right; color: var(--white); width: 180px; }
  .person-name { font-weight: 700; font-size: 21px; line-height: 1.1; }
  .person-title { font-weight: 500; font-size: 12px; margin-top: 2px; }
  .divider {
    width: 1px; height: 54px;
    background: var(--rule);
    margin: 0 18px;
  }
  .contacts { list-style: none; color: var(--white); font-size: 11.5px; }
  .contacts li { display: flex; align-items: center; gap: 8px; line-height: 17px; }
  .contacts svg { width: 10px; height: 10px; flex: none; }
  .address {
    position: absolute;
    left: 70px;
    top: 252px;
    font-size: 12.5px;
    font-weight: 500;
    color: var(--ink);
  }

  /* back */
  .pattern-field {
    position: absolute; inset: 0;
    background: linear-gradient(135deg, rgba(255,255,255,0.05), rgba(255,255,255,0.12));
  }
  .brand-back {
    position: absolute;
    right: 34px;
    top: 132px;
    display: flex;
    align-items: center;
    gap: 10px;
  }
  .brand-back .brand-mark {
    width: 28px; height: 28px;
    background: var(--white);
  }
  .brand-back .brand-name {
    color: var(--white);
    font-size: 26px;
    font-weight: 600;
  }
</style>
</head>
<body>
  <section class="card card-front" aria-label="Business card front">
    <div class="brand-front">
      <span class="brand-mark"></span>
      <span class="brand-name">VERODEX</span>
    </div>
    <div class="band">
      <div class="person">
        <p class="person-name">Mara Ellison</p>
        <p class="person-title">CEO &amp; Founder</p>
      </div>
      <span class="divider"></span>
      <ul class="contacts">
        <li>
          <svg viewBox="0 0 10 10"><path d="M2 1h2l1 2.5-1.2.8a5 5 0 0 0 2 2l.8-1.2L9 6v2a1 1 0 0 1-1 1A7 7 0 0 1 1 2a1 1 0 0 1 1-1z" fill="#ffffff"/></svg>
          (37) 555-0182
        </li>
        <li>
          <svg viewBox="0 0 10 10"><rect x="0.5" y="2" width="9" height="6" fill="#ffffff"/><path d="M0.5 2 5 5.5 9.5 2" fill="none" stroke="#4a7fcf" stroke-width="0.8"/></svg>
          info@verodex.com
        </li>
        <li>
          <svg viewBox="0 0 10 10"><circle cx="5" cy="5" r="4.3" fill="none" stroke="#ffffff" stroke-width="1"/><path d="M1 5h8M5 0.7c-2 2.5-2 6 0 8.6M5 0.7c2 2.5 2 6 0 8.6" fill="none" stroke="#ffffff" stroke-width="0.8"/></svg>
          www.verodex.com
        </li>
      </ul>
    </div>
    <p class="address">48 Harbor Lane, Suite 210, Linden, PA 18420</p>
  </section>

  <section class="card card-back" aria-label="Business card back">
    <div class="pattern-field" role="img" aria-label="Repeating brand pattern in soft blue tones"></div>
    <div class="brand-back">
      <span class="brand-mark"></span>
      <span class="brand-name">VERODEX</span>
    </div>
  </section>
</body>
</html>
```